Bramwell Specialty Coffee needs a Packaging design

We need packaging design for coffee that suits our brand identity, that is the best quality in Mexico.
We only sell mexican coffee with Q scores above 80
We are evaluating 3 types of packaging: Bag, Box and Cillinder can
The specific package format will be decided based on the designs that we get.

Target Market(s)

Coffee experts and enthusiast.
People that relate the Coffee consumption and experience with wine tasting and Bon Vivant way

Requirements
Should not have
• Photos any mexican cliché

```html
<!DOCTYPE html>
<html lang="en">
<head>
<meta charset="utf-8">
<title>Bramwell Specialty Coffee – Label</title>
<link href="https://fonts.googleapis.com/css2?family=Cormorant+Garamond:wght@600&family=Crimson+Text:ital,wght@0,600;1,600&display=swap" rel="stylesheet">
<style>
  :root {
    --paper-light: #f3ebdc;
    --paper-mid: #e2d2b4;
    --paper-deep: #c9b085;
    --band-gold: #c6a56c;
    --band-dark: #8a6d3c;
    --ink-brown: #5e4720;
    --mark-gold: #a98648;
    --canvas-white: #ffffff;
  }
  html, body {
    margin: 0;
    padding: 0;
    width: 1200px;
    height: 1110px;
    overflow: hidden;
    background: var(--canvas-white);
  }
  .label {
    position: relative;
    width: 1200px;
    height: 1000px;
    background: radial-gradient(ellipse at 55% 55%, var(--paper-light) 0%, var(--paper-mid) 60%, var(--paper-deep) 100%);
  }
  .key-band {
    position: absolute;
    left: 0;
    width: 1200px;
    background: linear-gradient(180deg, var(--band-gold), var(--band-dark) 50%, var(--band-gold));
  }
  .key-band--top { top: 0; height: 140px; }
  .key-band--bottom { top: 842px; height: 158px; }
  .brand-mark {
    position: absolute;
    left: 222px;
    top: 178px;
    width: 270px;
    height: 270px;
    border-radius: 50%;
    background: var(--mark-gold);
  }
  .brand-name {
    position: absolute;
    left: 520px;
    top: 205px;
    margin: 0;
    font-family: "Cormorant Garamond", Georgia, serif;
    font-weight: 600;
    color: var(--ink-brown);
    line-height: 1;
  }
  .brand-name__word {
    display: block;
    font-size: 136px;
  }
  .brand-name__line {
    display: block;
    margin: 22px 0 0 62px;
    font-size: 52px;
  }
  .roast-ornament {
    position: absolute;
    left: 430px;
    top: 455px;
    width: 340px;
    height: 285px;
  }
  .roast-name {
    position: absolute;
    left: 488px;
    top: 660px;
    margin: 0;
    font-family: "Crimson Text", Georgia, serif;
    font-style: italic;
    font-weight: 600;
    font-size: 15px;
    color: var(--ink-brown);
    transform: rotate(12deg);
  }
  .net-weight {
    position: absolute;
    left: 0;
    top: 778px;
    width: 1200px;
    margin: 0;
    text-align: center;
    font-family: "Crimson Text", Georgia, serif;
    font-weight: 600;
    font-size: 38px;
    line-height: 1;
    letter-spacing: 2px;
    color: var(--ink-brown);
  }
</style>
</head>
<body>
  <main class="label">
    <div class="key-band key-band--top" role="img" aria-label="Embossed gold Greek key border pattern"></div>

    <span class="brand-mark"></span>
    <h1 class="brand-name">
      <span class="brand-name__word">Bramwell</span>
      <span class="brand-name__line">Specialty Coffee</span>
    </h1>

    <svg class="roast-ornament" viewBox="0 0 340 285" role="img" aria-label="Gold flowing coffee bean ornament">
      <defs>
        <radialGradient id="bean-gold" cx="45%" cy="40%" r="70%">
          <stop offset="0%" stop-color="#e8d3a4"/>
          <stop offset="60%" stop-color="#b58f4c"/>
          <stop offset="100%" stop-color="#6f5326"/>
        </radialGradient>
      </defs>
      <ellipse cx="170" cy="150" rx="160" ry="112" transform="rotate(-20 170 150)" fill="url(#bean-gold)" opacity="0.55"/>
    </svg>
    <p class="roast-name">Special Bold Dark Roast</p>

    <p class="net-weight">NET WT 33.9 OZ(0.95kg)</p>

    <div class="key-band key-band--bottom" role="img" aria-label="Embossed gold Greek key border pattern"></div>
  </main>
</body>
</html>
```